Business Card Design Project

Looking for a logo and business card for a Real State Business i will be opening. The name is not choosen yet , but will probably be RWT IMOVEIS.
I was thinking black and silver colors, but am open to nice ideas.
I did add a business card that i liked a lot, am looking for something like that, with logo in black or silver in a black card. The logo i was thinking in the letters RWT as i uploaded or something or little and cute buildings or a house...just ideas, can be any nice logo.
Updates

You guys can add other colors if you want, I like colors very "BRIGHT" and "open", like red, pink, strong colors. almost glow in the dark colors. lol

Designers,

I've increased more 88 dollars in the budget for 1st place cause I will want envelope designs... small and big sizes.

So 1st place is now U$248,00. 

No need to send the envelope designs right now... only the business cards designs.

Thank you.

Industry/Entity Type

Business

Requirements
Must have
• Marcela Tavares Rocha

www.RWTimoveis-exemplo.com.br

+554187316042

marcela@rwtimoveis-exemplo.com.br

```html
<!DOCTYPE html>
<html lang="pt-BR">
<head>
<meta charset="utf-8">
<title>RWT IMOVEIS – Business Cards</title>
<link href="https://fonts.googleapis.com/css2?family=Josefin+Sans:wght@700&family=Quicksand:wght@400;600&display=swap" rel="stylesheet">
<style>
  :root {
    --bg: #4a4a4a;
    --card-dark: #231f20;
    --skyline-dark: #3a3839;
    --card-light: #ffffff;
    --skyline-light: #eef0ef;
    --pink: #ec008c;
    --white: #ffffff;
    --ink: #231f20;
  }
  * { margin: 0; padding: 0; box-sizing: border-box; }
  html, body { width: 1200px; height: 892px; overflow: hidden; }
  body {
    background: var(--bg);
    position: relative;
    font-family: "Quicksand", sans-serif;
  }
  .card {
    position: absolute;
    width: 620px;
    height: 370px;
    overflow: hidden;
  }
  /* Front card */
  .card-front {
    left: 500px;
    top: 60px;
    background: var(--card-dark);
  }
  .card-front .skyline {
    position: absolute;
    left: 0; bottom: 0;
    width: 100%; height: 140px;
    background: linear-gradient(to top, var(--skyline-dark) 55%, rgba(58,56,57,0.4));
  }
  .card-front .wordmark {
    position: absolute;
    left: 170px; top: 60px;
    font-family: "Josefin Sans", sans-serif;
    font-weight: 700;
    color: var(--pink);
    line-height: 0.95;
  }
  .wordmark .wordmark-initials { display: block; font-size: 132px; letter-spacing: 2px; }
  .wordmark .wordmark-rest { display: block; font-size: 68px; letter-spacing: 1px; }
  .card-front .tagline {
    position: absolute;
    left: 172px; top: 286px;
    font-size: 38px;
    font-weight: 400;
    color: var(--pink);
  }
  /* Back card */
  .card-back {
    left: 80px;
    top: 470px;
    background: var(--card-light);
  }
  .card-back .skyline {
    position: absolute;
    left: 0; bottom: 0;
    width: 100%; height: 130px;
    background: linear-gradient(to top, var(--skyline-light) 60%, rgba(238,240,239,0.3));
  }
  .brand-mark {
    position: absolute;
    left: 100px; top: 50px;
    display: flex; align-items: center; gap: 10px;
  }
  .brand-mark .brand-square {
    width: 22px; height: 22px; background: var(--pink);
  }
  .brand-mark .brand-name {
    font-weight: 600;
    font-size: 20px;
    color: var(--pink);
  }
  .contact {
    position: absolute;
    left: 250px; top: 40px;
  }
  .contact .person-name {
    font-weight: 600; font-size: 21px; color: var(--pink);
  }
  .contact .person-role {
    font-size: 17px; color: var(--ink); margin-top: 4px;
  }
  .contact-list {
    list-style: none; margin-top: 26px;
  }
  .contact-list li {
    display: flex; align-items: center; gap: 10px;
    font-size: 19px; color: var(--ink); line-height: 1.35;
  }
  .contact-list svg { width: 18px; height: 14px; flex: none; }
  .contact-list .website { font-size: 22px; }
</style>
</head>
<body>

  <section class="card card-front" aria-label="Front of business card">
    <div class="skyline" role="img" aria-label="City skyline silhouette"></div>
    <div class="wordmark">
      <span class="wordmark-initials">RWT</span>
      <span class="wordmark-rest">IMOVEIS</span>
    </div>
    <p class="tagline">Real Estate Agent</p>
  </section>

  <section class="card card-back" aria-label="Back of business card">
    <div class="skyline" role="img" aria-label="Faint city skyline silhouette"></div>
    <div class="brand-mark">
      <span class="brand-square"></span>
    </div>
    <div class="contact">
      <p class="person-name">Marcela Tavares Rocha</p>
      <p class="person-role">Real Estate Agent</p>
      <ul class="contact-list">
        <li>
          <svg viewBox="0 0 18 14" aria-hidden="true"><path d="M1 5c0-3 16-3 16 0v2h-4V5H5v2H1z M4 8h10l2 5H2z" fill="var(--pink)"/></svg>
          +55 4187 316 042
        </li>
        <li>
          <svg viewBox="0 0 18 14" aria-hidden="true"><rect x="1" y="1" width="16" height="12" fill="var(--pink)"/><path d="M1 1l8 7 8-7" stroke="#fff" stroke-width="1.5" fill="none"/></svg>
          marcela@rwtimoveis-exemplo.com.br
        </li>
        <li class="website">www.RWTimoveis-exemplo.com.br</li>
      </ul>
    </div>
  </section>

</body>
</html>
```